Web Design Project

Psychotherapy and Counselling Practice needs a landing page web design.

My business "Larkfield Advisory" specialises in the treatment of Anxiety and Depression with a holistic approach, endeavouring to unlock the key that holds us to ransom in a life that is imbalanced, frustrating, and ultimately of our own making due to our own perceptions and behaviours.

There is much that impacts us which we cannot change, but we are always in control of how we think, and how we frame our experiences.....learning to challenge those thoughts and behaviours that are destructive and disempowering opens up a world of joyful possibility. Life is about making choices, learn to make wiser and healthier choices.......

Larkfield Advisory has a client base of individual clients but will seek to expand to offer services to the Corporate world by offering an adjunct to employers for established "Wellness Programs".

Larkfield Advisory is a highly professional, ethically bound business, with the needs of the client at the forefront of all we do.

Larkfield Advisory wishes to avoid the usual "jargon driven" psychobabble offered on many counselling web pages. It aims to be stylishly presented, clean in look and with as few "words" as possible and a largely white background (faster loading and more powerful impact of what is stated), those words contained in the webpage should be meaningful, persuasive and have an impact simply at glance. Larkfield does not want , or expect, those prospective clients in need of support , to be reading through volumes of industry driven cliches.

At this point Larkfield is just looking for a high quality landing page. However in time this will likely expand to include other sections such as case studies, video content etc.

Target Market(s)

Those in need of emotional support, suffering mental health issues, and those simply wanting to become self aware supported by a mindful therapist.

Industry/Entity Type

Industry

Requirements
Must have
• The design must incorporate the Larkfield logo and colour schemes found on the attached files.

```html
<!DOCTYPE html>
<html lang="en">
<head>
<meta charset="utf-8">
<title>Larkfield Advisory</title>
<link href="https://fonts.googleapis.com/css2?family=Open+Sans:wght@400;600;700&display=swap" rel="stylesheet">
<style>
:root{
  --green:#8aa631;
  --green-dark:#7a9527;
  --green-text:#8fae2c;
  --header:#717171;
  --band:#ebebeb;
  --panel:#f0f0f0;
  --text:#555;
  --muted:#a0a0a0;
  --ink:#2e2e2e;
  --white:#fff;
}
*{margin:0;padding:0;box-sizing:border-box}
html,body{width:795px;height:1200px;overflow:hidden}
body{position:relative;background:var(--white);font-family:"Open Sans",sans-serif;color:var(--text)}
.abs{position:absolute}

.site-header{left:0;top:0;width:795px;height:126px;background:var(--header)}
.brand{left:86px;top:50px;display:flex;align-items:center;gap:6px;color:#a8c34a;font-size:15px;font-weight:400;letter-spacing:.5px;text-transform:uppercase}
.brand-mark{width:9px;height:9px;border-radius:50%;background:#a8c34a}
.contact-top{right:86px;top:38px;text-align:right;color:var(--white)}
.contact-top .phone{font-size:16px;font-weight:600;letter-spacing:.3px;line-height:22px}
.contact-top .email{font-size:10.5px;line-height:15px}

.main-nav{left:86px;top:85px;width:623px;height:41px;background:linear-gradient(#99b53c,var(--green-dark));display:flex;align-items:center;padding-left:25px}
.main-nav a{color:var(--white);text-decoration:none;font-size:12px;margin-right:24px}
.search{left:534px;top:97px;width:164px;height:17px;background:var(--white);border-radius:2px;font-size:5.5px;color:#aaa;padding:5px 6px}
.search svg{position:absolute;right:5px;top:4px}

.hero-band{left:0;top:126px;width:795px;height:278px;background:var(--band)}
.hero{left:86px;top:138px;width:623px;height:244px;background:linear-gradient(180deg,#a98c86 0%,#d7a88e 45%,#c1826c 62%,#5f4236 100%)}
.hero-title{left:100px;top:222px;color:var(--white);font-size:38px;line-height:37px;font-weight:400;text-shadow:0 1px 3px rgba(0,0,0,.25)}
.dots{left:113px;top:335px;display:flex;gap:2px}
.dots i{width:9px;height:9px;border-radius:50%;background:#333;border:1px solid #bbb}
.dots i:first-child{background:var(--white)}

.tile{top:421px;width:199px;height:101px;overflow:hidden}
.tile .photo{width:100%;height:100%}
.tile .label{position:absolute;left:0;bottom:7px;width:100%;height:28px;background:var(--green);color:var(--white);font-size:10.5px;text-align:center;line-height:28px}

.welcome{left:86px;top:534px;width:411px;height:122px;background:#050505}
.welcome .photo{position:absolute;left:0;top:0;width:200px;height:122px;background:linear-gradient(90deg,#4a4440 0%,#2c2826 55%,#050505 100%)}
.welcome h1{position:absolute;left:198px;top:46px;color:var(--white);font-weight:400;font-size:11.5px;line-height:15px}
.welcome h1 span{display:block;font-size:18px;line-height:22px}
.welcome h1 em{font-style:normal;color:#9dbb3a}

.intro{left:86px;top:662px;width:411px;font-size:8.1px;line-height:13.2px;text-align:justify;color:#5a5a5a}
.intro p+p{margin-top:13px}
.intro a{color:var(--green-text);font-weight:600;text-decoration:none}

.news{left:510px;top:534px;width:199px;height:284px;background:var(--panel)}
.news h2{position:absolute;left:13px;top:12px;font-size:10.5px;font-weight:400;color:var(--green-text)}
.news-item{position:absolute;left:15px;width:170px}
.news-item .thumb{position:absolute;left:0;top:0;width:56px;height:46px}
.news-item h3{margin-left:60px;font-size:8px;font-weight:400;color:#444;line-height:11px}
.news-item p{margin-left:60px;margin-top:3px;font-size:6px;line-height:12px;color:var(--muted);text-align:justify}
.news-item a{display:block;text-align:right;font-size:6px;color:#b7cc74;text-decoration:none;line-height:10px}

.newsletter{left:86px;top:842px;width:623px;height:70px;background:var(--green)}
.newsletter h2{position:absolute;left:25px;top:19px;color:var(--white);font-weight:400;font-size:13.5px}
.newsletter p{position:absolute;left:26px;top:40px;color:var(--white);font-size:8px}
.newsletter .field{position:absolute;left:228px;top:21px;width:296px;height:27px;background:var(--white);font-size:6.5px;color:#999;padding:9px 11px}
.newsletter .submit{position:absolute;left:537px;top:22px;width:68px;height:25px;background:var(--ink);color:var(--white);font-size:8px;font-weight:700;text-align:center;line-height:25px}

.partners{left:86px;top:930px;width:623px;height:66px;display:flex;justify-content:space-between;align-items:center}
.partner{background:#dfe6cc;border-radius:6px}

.site-footer{left:0;top:1018px;width:795px;height:148px;background:var(--band)}
.col{top:14px}
.col h4{font-size:10.5px;font-weight:400;color:var(--green-text);margin-bottom:14px}
.col li{list-style:none;font-size:8px;line-height:13.2px;color:#555}
.col.support li{line-height:16px}
.col.contact li{line-height:16px}
.col.contact li:first-child{font-weight:600}
.col.social h4{color:#444}
.social-row{display:flex;align-items:center;justify-content:space-between;width:92px;height:24px;font-size:8px;color:#555}
.social-row i{width:18px;height:18px;border-radius:50%;background:var(--white);border:1px solid #ddd}

.legal{left:0;top:1166px;width:795px;height:34px;background:#e4e4e4;border-top:1px solid #d6d6d6;font-size:7.5px;text-align:center;line-height:34px;color:#555}
</style>
</head>
<body>

<header class="site-header abs">
  <div class="brand abs"><span class="brand-mark"></span>Larkfield Advisory</div>
  <div class="contact-top abs">
    <div class="phone">Phone&nbsp; : 1-800-5716-318</div>
    <div class="email">Email: info@larkfieldadvisory.com</div>
  </div>
</header>

<nav class="main-nav abs">
  <a href="#">Home</a><a href="#">About Us</a><a href="#">Services</a><a href="#">Testimonials</a><a href="#">FAQ's</a><a href="#">Contact Us</a>
</nav>
<div class="search abs">Type search
  <svg width="9" height="9" viewBox="0 0 10 10"><circle cx="4" cy="4" r="3" fill="none" stroke="#aaa" stroke-width="1.2"/><line x1="6.2" y1="6.2" x2="9" y2="9" stroke="#aaa" stroke-width="1.4"/></svg>
</div>

<div class="hero-band abs"></div>
<div class="hero abs" role="img" aria-label="Photo of a person sitting alone with head on knees on a beach at sunset"></div>
<div class="hero-title abs">Anxiety &amp;<br>Depression</div>
<div class="dots abs"><i></i><i></i><i></i><i></i></div>

<div class="tile abs" style="left:86px">
  <div class="photo" role="img" aria-label="Photo of a group of office workers" style="background:linear-gradient(90deg,#5a5c63,#b9bcc2 50%,#4c4f56)"></div>
  <div class="label">Workplace Stress</div>
</div>
<div class="tile abs" style="left:298px">
  <div class="photo" role="img" aria-label="Photo of a counselling session between two women" style="background:linear-gradient(90deg,#d9c7a4,#b18c6a 50%,#e3dccd)"></div>
  <div class="label">Counselling</div>
</div>
<div class="tile abs" style="left:510px">
  <div class="photo" role="img" aria-label="Photo of a stressed woman at a computer" style="background:linear-gradient(90deg,#8d9096,#e5ddd3 45%,#cfae92)"></div>
  <div class="label">Anxiety &amp; Depression</div>
</div>

<section class="welcome abs">
  <div class="photo" role="img" aria-label="Photo of a woman sitting on the floor hugging her knees"></div>
  <h1>Welcome To <span><em>Larkfield</em> Advisory</span></h1>
</section>

<div class="intro abs">
  <p>Sed ut perspiciatis unde omnis iste natus error sit voluptatem accusantium doloremque laudantium, totam rem aperiam, eaque ipsa quae ab illo inventore veritatis et quasi architecto beatae vitae dicta sunt explicabo. Nemo enim ipsam voluptatem quia voluptas sit aspernatur aut odit aut fugit, sed quia consequuntur magni dolores eos qui ratione voluptatem sequi nesciunt. Neque porro quisquam est, qui dolorem ipsum quia dolor sit amet, consectetur, adipisci velit, sed quia non numquam eius modi tempora incidunt ut labore et dolore magnam aliquam quaerat voluptatem.</p>
  <p>Ut enim ad minima veniam, quis nostrum exercitationem ullam corporis suscipit laboriosam, Sed ut perspiciatis unde omnis iste natus error sit voluptatem accusantium doloremque laudantium, totam rem aperiam, eaque ipsa quae ab illo inventore veritatis et quasi architecto beatae vitae dicta sunt explicabo. Nemo enim ipsam voluptatem quia voluptas sit aspernatur aut odit aut fugit, sed quia consequuntur magni dolores eos qui ratione voluptatem sequi nesciunt. <a href="#">Read More</a></p>
</div>

<aside class="news abs">
  <h2>Latest News</h2>
  <div class="news-item" style="top:42px">
    <div class="thumb" role="img" aria-label="Photo of a worried woman" style="background:linear-gradient(90deg,#c9c4bd,#8f8a85)"></div>
    <h3>At vero eos et accusamus</h3>
    <p>It is a long established fact that a reader will be distracted by the readable content of a page when looking at its layout.</p>
    <a href="#">Read More &gt;&gt;</a>
  </div>
  <div class="news-item" style="top:118px">
    <div class="thumb" role="img" aria-label="Photo of two women in conversation" style="background:linear-gradient(90deg,#8a5b45,#d9b79e)"></div>
    <h3>At vero eos et accusamus</h3>
    <p>It is a long established fact that a reader will be distracted by the readable content of a page when looking at its layout.</p>
    <a href="#">Read More &gt;&gt;</a>
  </div>
  <div class="news-item" style="top:200px">
    <div class="thumb" role="img" aria-label="Photo of a woman holding her head" style="background:linear-gradient(90deg,#d7ccc4,#3d2f2c)"></div>
    <h3>At vero eos et accusamus</h3>
    <p>It is a long established fact that a reader will be distracted by the readable content of a page when looking at its layout.</p>
    <a href="#">Read More &gt;&gt;</a>
  </div>
</aside>

<section class="newsletter abs">
  <h2>Sign up for Newsletter</h2>
  <p>Get a weekly Updates Through E-mail</p>
  <div class="field">Enter Your E-mail address</div>
  <div class="submit">SUBMIT</div>
</section>

<div class="partners abs">
  <div class="partner" style="width:104px;height:40px"></div>
  <div class="partner" style="width:132px;height:54px"></div>
  <div class="partner" style="width:86px;height:58px"></div>
  <div class="partner" style="width:66px;height:56px;border-radius:50%"></div>
  <div class="partner" style="width:120px;height:66px"></div>
</div>

<footer class="site-footer abs">
  <div class="col abs" style="left:86px">
    <h4>Quick Links</h4>
    <ul><li>Home</li><li>About Us</li><li>Services</li><li>Testimonials</li><li>FAQ's</li><li>Contact Us</li></ul>
  </div>
  <div class="col support abs" style="left:246px">
    <h4>Support Links</h4>
    <ul><li>Legal Notice</li><li>Privacy Policy</li><li>Terms &amp; Conditions</li><li>Help</li></ul>
  </div>
  <div class="col contact abs" style="left:404px">
    <h4>Contact Us</h4>
    <ul>
      <li>Hollis Marsh Consultancy</li>
      <li>14 Alder Lane, Westbrook Falls</li>
      <li>Phone: 1-800-5716-318</li>
      <li>Email: info@larkfieldadvisory.com</li>
      <li>Website: www.larkfieldadvisory.com</li>
    </ul>
  </div>
  <div class="col social abs" style="left:617px">
    <h4>Connect With Us</h4>
    <div class="social-row"><i></i>Updates</div>
    <div class="social-row"><i></i>Community</div>
    <div class="social-row"><i></i>Network</div>
  </div>
</footer>

<div class="legal abs">Copyright ©2013 Larkfield Advisory &nbsp;- All rights reserved</div>

</body>
</html>
```